Emerging automotive detailing business

I am starting a small automotive detailing business in hopes of becoming a well-known detailer to work on high end cars. I would like a card to reflect the high quality and time I put into my work. The name of the company is Bright Crest Detailing. I feel like it represents racecars getting off the line at the drag strip as well as an innuendo of "Up the Ladder". I do minor paint correction such as clay barring, multi-step buffing and polishing, waxing, hand washes, etc. I am always striving to learn more and improve my work. My goal is to have total customer satisfaction. This is a female run business but I do not want it to be very girly. Elegant is okay! I have pictures of my personal wrenfield attached, they do not need to be incorporated but if you can think of a cool way to use 1 or all of them, go for it!

Target Market(s)

Anyone that owns a vehicle. Preferably high end vehicles such as Valtori, Castellverde and Morvani but I will also happily work on any car, truck or suv no matter what brand.

Industry/Entity Type

Automotive

Contact Information for Business Card

Bright Crest Detailing
Mira Tolland
4175 Quenhollow Rd
Ashmere PA 17492
Cell phone- call/text- 717-555-0148
email- brightcrestdetails@maildrop-example.com
Instagram: @brightcrestdetailing
Facebook: facebook.com/brightcrestdetailing

Requirements
Must have
• Business name, my name, address, phone number. Listing that I do minor paint correction such as clay barring, multi-step buffing and polishing, waxing, hand washes, interior cleaning, and more. (This last part was in nice to haves but I have realized that I do really want it, so I moved it to must haves.) I want something that is different and eye-catching to my customers. Some people have done this very well with cards already submitted to me, but a lot have not. I didn't mess with the "look and feel bars" much because because I am pretty open to the overall design as long as it is not your basic run of the mill design.
Nice to have
• Something car related. Maybe an appointment time/date line. I do not have a logo, but if you would like to design one and incorporate it, that would be amazing!
Should not have
• Purple and Pink colors. Boring, basic, normal card.

```html
<!DOCTYPE html>
<html lang="en">
<head>
<meta charset="utf-8">
<title>Bright Crest Detailing — Business Card</title>
<link rel="stylesheet" href="https://fonts.googleapis.com/css2?family=Arimo:ital,wght@0,400;1,400&family=Tinos&display=swap">
<style>
  :root {
    --stage: #e9e7e3;
    --paper: #f4f4f3;
    --ink: #1c1c1c;
    --muted: #4a5256;
    --slate: #374145;
    --band-black: #141414;
    --band-text: #e6e9ea;
    --icon: #2a2a2a;
    --rule: #9aa2a5;
  }
  * { box-sizing: border-box; margin: 0; padding: 0; }
  html, body { width: 1200px; height: 892px; overflow: hidden; }
  body {
    background: var(--stage);
    font-family: "Arimo", Arial, sans-serif;
    color: var(--ink);
    position: relative;
  }
  .card {
    position: absolute;
    left: 300px;
    width: 600px;
    height: 343px;
    background: var(--paper);
    box-shadow: 0 6px 18px rgba(0,0,0,0.18);
    overflow: hidden;
  }
  .card--front { top: 60px; }
  .card--back { top: 489px; }

  /* Front */
  .front__title {
    position: absolute;
    top: 62px; left: 0; right: 0;
    text-align: center;
    font-family: "Tinos", "Times New Roman", serif;
    font-weight: 400;
    font-size: 38px;
    letter-spacing: 0.5px;
  }
  .front__name {
    position: absolute;
    top: 114px; left: 0; right: 0;
    text-align: center;
    font-size: 24px;
    letter-spacing: 0.5px;
  }
  .front__services {
    position: absolute;
    top: 166px; left: 60px; right: 60px;
    padding-top: 12px;
    border-top: 1px solid var(--rule);
    text-align: center;
    font-size: 12.5px;
    line-height: 1.6;
    letter-spacing: 1.2px;
    text-transform: uppercase;
    color: var(--muted);
  }
  .front__band {
    position: absolute;
    left: 0; right: 0; bottom: 0;
    height: 90px;
    background: var(--slate);
    display: flex;
    align-items: center;
    justify-content: space-between;
    padding: 0 22px;
    color: var(--band-text);
    font-size: 15px;
  }
  .front__band .phone { font-style: italic; }

  /* Back */
  .back__strip {
    position: absolute;
    top: 0; bottom: 0; left: 0;
    width: 34px;
    background: var(--band-black);
  }
  .back__heading {
    position: absolute;
    top: 58px; right: 50px;
    text-align: right;
  }
  .back__title { font-size: 30px; font-weight: 400; }
  .back__name { font-size: 26px; margin-top: 10px; }
  .back__contacts {
    position: absolute;
    left: 70px; bottom: 52px;
    list-style: none;
    font-size: 17px;
    line-height: 1.45;
  }
  .back__contacts li { display: flex; align-items: center; gap: 10px; }
  .back__contacts svg { width: 13px; height: 13px; flex: none; }
</style>
</head>
<body>

<section class="card card--front" aria-label="Card front">
  <h1 class="front__title">Bright Crest Detailing</h1>
  <p class="front__name">Mira Tolland</p>
  <p class="front__services">Clay Barring · Multi-Step Buffing &amp; Polishing · Waxing<br>Hand Washes · Interior Cleaning &amp; More</p>
  <div class="front__band">
    <span class="phone">717-555-0148</span>
    <span class="social">@brightcrestdetailing</span>
    <span class="email">brightcrestdetails@maildrop-example.com</span>
  </div>
</section>

<section class="card card--back" aria-label="Card back">
  <div class="back__strip"></div>
  <div class="back__heading">
    <h2 class="back__title">Bright Crest Detailing</h2>
    <p class="back__name">Mira Tolland</p>
  </div>
  <ul class="back__contacts">
    <li>
      <svg viewBox="0 0 13 13" aria-hidden="true"><rect width="13" height="13" fill="var(--icon)"/><rect x="4" y="2.5" width="5" height="8" rx="1" fill="#fff"/></svg>
      717-555-0148
    </li>
    <li>
      <svg viewBox="0 0 13 13" aria-hidden="true"><rect width="13" height="13" fill="var(--icon)"/><circle cx="6.5" cy="6.5" r="3.2" fill="none" stroke="#fff" stroke-width="1.4"/></svg>
      @brightcrestdetailing
    </li>
    <li>
      <svg viewBox="0 0 13 13" aria-hidden="true"><rect width="13" height="13" fill="var(--icon)"/><rect x="2.5" y="4" width="8" height="5.5" fill="#fff"/><path d="M2.5 4 L6.5 7 L10.5 4" fill="none" stroke="var(--icon)" stroke-width="1"/></svg>
      brightcrestdetails@maildrop-example.com
    </li>
    <li>
      <svg viewBox="0 0 13 13" aria-hidden="true"><rect width="13" height="13" fill="var(--icon)"/><path d="M6.5 2.5a2.8 2.8 0 0 1 2.8 2.8c0 2-2.8 5.2-2.8 5.2S3.7 7.3 3.7 5.3A2.8 2.8 0 0 1 6.5 2.5z" fill="#fff"/></svg>
      4175 Quenhollow Rd, Ashmere PA 17492
    </li>
  </ul>
</section>

</body>
</html>
```